Business Card for Coastal Tundrabridge Advisory

We need a business card for Coastal Tundrabridge Advisory. The company website address is provided below. The company logo is attached. We provide specialized permafrost services to the mining, transportation, and oil & gas industries. The card should be prepared for:
Matthias Korhonen, PhD.
Coastal Tundrabridge Advisory
PO Box 418259
Quillwater, Alaska 99642
Direct: +1-907-555-0143
Email: mkorhonen@tundrabridgeadvisory.example
Website: www.coastaltundrabridgeadvisory.example

```html
<!DOCTYPE html>
<html lang="en">
<head>
<meta charset="utf-8">
<title>Coastal Tundrabridge Advisory – Business Card</title>
<link rel="stylesheet" href="https://fonts.googleapis.com/css2?family=Roboto:wght@300;400;500;700&display=swap">
<style>
  :root {
    --backdrop: #232323;
    --card: #111722;
    --ink: #ffffff;
    --ink-soft: #e3e6ec;
    --brand-muted: #2b3447;
    --rule: #8a909c;
  }
  * { margin: 0; padding: 0; box-sizing: border-box; }
  html, body {
    width: 1200px; height: 711px; overflow: hidden;
    background: var(--backdrop);
    font-family: "Roboto", Arial, sans-serif;
  }
  .canvas { position: relative; width: 1200px; height: 711px; }
  .card {
    position: absolute; top: 207px;
    width: 520px; height: 297px;
    background: var(--card);
    color: var(--ink);
  }
  .card--front { left: 50px; }
  .card--back { left: 630px; }

  /* Front */
  .brand {
    position: absolute; left: 0; right: 0; top: 92px;
    text-align: center;
  }
  .brand__name {
    font-weight: 500; font-size: 24px; letter-spacing: 3px;
    text-transform: uppercase; color: var(--brand-muted); line-height: 1.25;
  }
  .services {
    position: absolute; left: 20px; right: 20px; bottom: 30px;
    text-align: center;
  }
  .services__title { font-weight: 500; font-size: 10px; letter-spacing: .3px; margin-bottom: 3px; }
  .services__text { font-weight: 400; font-size: 9.5px; color: var(--ink-soft); }

  /* Back */
  .person {
    position: absolute; left: 30px; top: 128px; width: 230px;
    text-align: right;
  }
  .person__name { font-size: 26px; line-height: 1; white-space: nowrap; }
  .person__first { font-weight: 700; }
  .person__last { font-weight: 300; }
  .person__title { display: block; font-weight: 700; font-size: 14px; margin-top: 4px; }
  .divider {
    position: absolute; left: 282px; top: 92px;
    width: 1px; height: 82px; background: var(--rule);
  }
  .contacts {
    position: absolute; left: 296px; top: 104px;
    list-style: none; font-size: 8.6px; font-weight: 400; color: var(--ink-soft);
  }
  .contacts li { display: flex; align-items: center; gap: 6px; margin-bottom: 8px; white-space: nowrap; }
  .contacts svg { width: 10px; height: 10px; flex: none; }
  .address {
    position: absolute; left: 0; right: 0; bottom: 44px;
    text-align: center; font-size: 10.5px; font-weight: 400; color: var(--ink-soft);
    padding-left: 150px;
  }
</style>
</head>
<body>
<main class="canvas">
  <section class="card card--front" aria-label="Card front">
    <div class="brand">
      <p class="brand__name">Coastal Tundrabridge<br>Advisory</p>
    </div>
    <div class="services">
      <p class="services__title">OUR SERVICES</p>
      <p class="services__text">We provide specialized permafrost services to the mining, transportation, and oil &amp; gas industries</p>
    </div>
  </section>

  <section class="card card--back" aria-label="Card back">
    <div class="person">
      <p class="person__name"><span class="person__first">Matthias</span> <span class="person__last">Korhonen</span></p>
      <span class="person__title">PhD</span>
    </div>
    <div class="divider"></div>
    <ul class="contacts">
      <li>
        <svg viewBox="0 0 24 24" aria-hidden="true"><path fill="#fff" d="M6.6 10.8a15.1 15.1 0 0 0 6.6 6.6l2.2-2.2c.3-.3.7-.4 1-.2 1.1.4 2.3.6 3.6.6.6 0 1 .4 1 1V20c0 .6-.4 1-1 1A17 17 0 0 1 3 4c0-.6.4-1 1-1h3.5c.6 0 1 .4 1 1 0 1.3.2 2.5.6 3.6.1.3 0 .7-.2 1z"/></svg>
        +1-907-555-0143
      </li>
      <li>
        <svg viewBox="0 0 24 24" aria-hidden="true"><path fill="#fff" d="M3 5h18a1 1 0 0 1 1 1v12a1 1 0 0 1-1 1H3a1 1 0 0 1-1-1V6a1 1 0 0 1 1-1zm1 2.2V17h16V7.2l-8 5.3z"/></svg>
        mkorhonen@tundrabridgeadvisory.example
      </li>
      <li>
        <svg viewBox="0 0 24 24" aria-hidden="true"><circle cx="12" cy="12" r="9" fill="none" stroke="#fff" stroke-width="2"/><path d="M3 12h18M12 3c3 3 3 15 0 18M12 3c-3 3-3 15 0 18" fill="none" stroke="#fff" stroke-width="1.5"/></svg>
        www.coastaltundrabridgeadvisory.example
      </li>
    </ul>
    <p class="address">PO Box 418259 Quillwater, Alaska 99642</p>
  </section>
</main>
</body>
</html>
```